Card Design for my dog training business Brightpaw Obedience

Need a business card design for my dog training business with my new logo. Want the card to come off professional yet fun. Want it to be very eye catchy as well. I normally have these at vet clinics, pet stores, and groomers. so need it to look better than my competitors.
Target Market(s)
dog owners
Industry/Entity Type
Dog Training
Contact Information for Business Card
needs logo, my name and info
Font styles to use
Serif
Colors
0255a3
ffffff
ec1f27
000000
333333
fbfbfb
Requirements
Must have
- Brightpaw Obedience
- Felix Orland
- 415 903 2276
- info@brightpawobedience.example
- www.brightpawobedience.example

```html
<!DOCTYPE html>
<html lang="en">
<head>
<meta charset="utf-8">
<title>Brightpaw Obedience – Business Card</title>
<link rel="stylesheet" href="https://fonts.googleapis.com/css2?family=Noto+Serif:wght@400&family=EB+Garamond:ital@1&family=Quattrocento+Sans&display=swap">
<style>
  :root {
    --brand-blue: #0255a3;
    --brand-red: #ec1f27;
    --paper: #fbfbfb;
    --ink: #333333;
    --ink-dark: #000000;
    --white: #ffffff;
    --backdrop: #e6e6e6;
  }
  * { box-sizing: border-box; margin: 0; padding: 0; }
  html, body {
    width: 1200px; height: 576px; overflow: hidden;
    background: var(--backdrop);
  }
  .stage { position: relative; width: 1200px; height: 576px; }
  .card {
    position: absolute; top: 138px;
    width: 484px; height: 294px;
    background: var(--paper);
    border-radius: 12px;
    overflow: hidden;
    box-shadow: 0 2px 5px rgba(0,0,0,0.18);
  }
  .card--front { left: 82px; }
  .card--back { left: 602px; height: 292px; }

  .wordmark {
    position: absolute;
    text-align: center;
    font-family: "Noto Serif", Georgia, serif;
    font-weight: 400;
    color: var(--ink);
    line-height: 1.15;
  }
  .wordmark__dot {
    display: block; margin: 0 auto 12px;
    width: 16px; height: 16px; border-radius: 50%;
    background: var(--ink);
  }
  .card--front .wordmark { left: 0; right: 0; top: 84px; font-size: 30px; }
  .card--back .wordmark { left: 20px; width: 180px; top: 100px; font-size: 22px; }

  .tagline {
    font-family: "EB Garamond", Georgia, serif;
    font-style: italic;
    color: var(--white);
    font-size: 12.5px;
    white-space: nowrap;
  }
  .front-band {
    position: absolute; left: 0; right: 0; top: 256px; height: 28px;
    background: var(--brand-blue);
    display: flex; align-items: center; justify-content: center;
  }

  .contact { position: absolute; left: 259px; top: 78px; }
  .contact__name {
    font-family: "Noto Serif", Georgia, serif;
    font-size: 20px; color: var(--brand-blue); font-weight: 400;
  }
  .contact__role {
    font-family: "Quattrocento Sans", Arial, sans-serif;
    font-size: 12px; color: var(--ink); margin-top: 2px;
  }
  .contact__list { list-style: none; margin-top: 18px; }
  .contact__item {
    display: flex; align-items: center; gap: 10px;
    font-family: "Quattrocento Sans", Arial, sans-serif;
    font-size: 11.5px; color: var(--ink);
    height: 19px;
  }
  .contact__icon { width: 12px; height: 12px; flex: none; }

  .back-footer { position: absolute; left: 0; bottom: 0; width: 484px; height: 38px; }
  .back-footer .tagline { position: absolute; right: 30px; top: 8px; }
</style>
</head>
<body>
<main class="stage">

  <section class="card card--front" aria-label="Business card front">
    <div class="wordmark"><span class="wordmark__dot"></span>Brightpaw<br>Obedience</div>
    <div class="front-band">
      <p class="tagline">“Teaching good manners one happy dog at a time.”</p>
    </div>
  </section>

  <section class="card card--back" aria-label="Business card back">
    <div class="wordmark"><span class="wordmark__dot"></span>Brightpaw<br>Obedience</div>

    <div class="contact">
      <h1 class="contact__name">Felix Orland</h1>
      <p class="contact__role">Dog Trainer</p>
      <ul class="contact__list">
        <li class="contact__item">
          <svg class="contact__icon" viewBox="0 0 12 12" aria-hidden="true">
            <path fill="#0255a3" d="M1 4.5C1 3 3 1.5 6 1.5s5 1.5 5 3v1H8.5V4.2H3.5v1.3H1z"/>
            <path fill="#0255a3" d="M3 6.5h6l1.5 4h-9z"/>
          </svg>
          415 903 2276
        </li>
        <li class="contact__item">
          <svg class="contact__icon" viewBox="0 0 12 12" aria-hidden="true">
            <rect x="0.5" y="2.5" width="11" height="7.5" fill="#0255a3"/>
            <path d="M1 3l5 4 5-4" fill="none" stroke="#fbfbfb" stroke-width="1"/>
          </svg>
          info@brightpawobedience.example
        </li>
        <li class="contact__item">
          <svg class="contact__icon" viewBox="0 0 12 12" aria-hidden="true">
            <circle cx="6" cy="6" r="5" fill="#0255a3"/>
            <path d="M1 6h10M6 1c-2 2.5-2 7.5 0 10M6 1c2 2.5 2 7.5 0 10" fill="none" stroke="#fbfbfb" stroke-width="0.7"/>
          </svg>
          www.brightpawobedience.example
        </li>
      </ul>
    </div>

    <div class="back-footer">
      <svg width="484" height="38" viewBox="0 0 484 38" aria-hidden="true">
        <rect x="0" y="26" width="200" height="12" fill="#ec1f27"/>
        <path d="M194 38 L208 6 Q211 0 218 0 H484 V38 Z" fill="#0255a3"/>
      </svg>
      <p class="tagline">“Teaching good manners one happy dog at a time.”</p>
    </div>
  </section>

</main>
</body>
</html>
```